Heron Loan Partners Business Card

We need a business card design for our mortgage servicing company. In addition to servicing the loans of homeowners, we help homeowners with purchasing their homes and any mortgage refinancing. We would like to see designs that use the colors in the logo attached below (gold-ish yellow and navy blue), and any other design you deem fit! The design should communicate a simpler life with smart mortgages provided by Heron.

```html
<!DOCTYPE html>
<html lang="en">
<head>
<meta charset="utf-8">
<title>Heron Loan Partners Business Card</title>
<link href="https://fonts.googleapis.com/css2?family=Lato:wght@400;700&display=swap" rel="stylesheet">
<style>
  :root {
    --gold: #e2aa2c;
    --navy: #2b2763;
    --ink: #4a4a4a;
    --paper: #ffffff;
    --backdrop: #e4e5e7;
  }
  * { margin: 0; padding: 0; box-sizing: border-box; }
  html, body { width: 1200px; height: 800px; overflow: hidden; }
  body {
    background: var(--backdrop);
    font-family: "Lato", sans-serif;
    display: flex;
    align-items: center;
    justify-content: center;
    gap: 60px;
  }
  .card {
    position: relative;
    width: 525px;
    height: 300px;
    background: var(--paper);
    box-shadow: 0 2px 6px rgba(0,0,0,0.12);
  }
  .card-front {
    display: flex;
    align-items: center;
    justify-content: center;
  }
  .wordmark {
    display: flex;
    align-items: center;
    gap: 10px;
    color: var(--navy);
    font-weight: 700;
    font-size: 30px;
    letter-spacing: 0.5px;
  }
  .wordmark-dot {
    width: 16px;
    height: 16px;
    border-radius: 50%;
    background: var(--gold);
  }
  .card-back .wordmark {
    position: absolute;
    top: 58px;
    right: 34px;
    font-size: 20px;
    gap: 8px;
  }
  .card-back .wordmark-dot { width: 11px; height: 11px; }
  .holder {
    position: absolute;
    top: 48px;
    left: 40px;
  }
  .holder-name {
    color: var(--gold);
    font-size: 15px;
    letter-spacing: 0.5px;
    text-transform: uppercase;
  }
  .holder-title {
    color: var(--ink);
    font-size: 13px;
    margin-top: 1px;
  }
  .rule {
    position: absolute;
    top: 104px;
    left: 40px;
    right: 34px;
    height: 1px;
    background: var(--gold);
  }
  .contacts {
    position: absolute;
    top: 124px;
    left: 40px;
    list-style: none;
  }
  .contacts li {
    display: flex;
    align-items: center;
    gap: 8px;
    color: var(--ink);
    font-size: 13px;
    line-height: 22px;
  }
  .contacts svg { width: 11px; height: 11px; fill: var(--navy); flex: none; }
</style>
</head>
<body>
  <section class="card card-front">
    <div class="wordmark"><span class="wordmark-dot"></span>Heron Loan Partners</div>
  </section>

  <section class="card card-back">
    <div class="holder">
      <div class="holder-name">John Smith</div>
      <div class="holder-title">Director</div>
    </div>
    <div class="rule"></div>
    <div class="wordmark"><span class="wordmark-dot"></span>Heron Loan Partners</div>
    <ul class="contacts">
      <li>
        <svg viewBox="0 0 12 12"><path d="M2.5 0.5 L4.5 0.5 L5.2 3.2 L3.8 4.3 Q5 7 7.7 8.2 L8.8 6.8 L11.5 7.5 L11.5 9.5 Q11.5 11.5 9.5 11.5 Q0.5 10.5 0.5 2.5 Q0.5 0.5 2.5 0.5 Z"/></svg>
        300-200-9000
      </li>
      <li>
        <svg viewBox="0 0 12 12"><path d="M0 2 H12 V10 H0 Z M1 3 L6 7 L11 3 V9 H1 Z" fill-rule="evenodd"/></svg>
        info@heronloanpartners.com
      </li>
      <li>
        <svg viewBox="0 0 12 12"><circle cx="6" cy="6" r="5.3" fill="none" stroke="#2b2763" stroke-width="1.2"/><ellipse cx="6" cy="6" rx="2.2" ry="5.3" fill="none" stroke="#2b2763" stroke-width="1"/><path d="M0.7 6 H11.3" stroke="#2b2763" stroke-width="1"/></svg>
        www.heronloanpartners.com
      </li>
      <li>
        <svg viewBox="0 0 12 12"><path d="M6 0 A4.2 4.2 0 0 1 10.2 4.2 C10.2 7 6 12 6 12 C6 12 1.8 7 1.8 4.2 A4.2 4.2 0 0 1 6 0 Z M6 2.6 A1.6 1.6 0 1 0 6 5.8 A1.6 1.6 0 1 0 6 2.6 Z" fill-rule="evenodd"/></svg>
        00 dummy city, place 0000
      </li>
    </ul>
  </section>
</body>
</html>
```